Unravelling Markets - Podcast Cover

Unravelling Markets is a weekly podcast that dispels some of the myths about conventional economic thinking and provides a new way of thinking about issues that are faced by the global economy. It's insightful, thought-provoking and, most importantly, fun. We are refreshing the look and sound of the podcast. I have attached a copy of the old amateur design (which I did!)

Target Market(s)

Male oriented, smart folk with an interest in politics and economics

Font styles to use
Sans Serif

Requirements
Must have
• Clearly visible title, even when reduced in size. Must be 3000 pixels by 3000 pixels.
Nice to have
• This podcast challenges the status quo. It should reflect that. Photos and names of the hosts. Actually, because th ephotos are so different, we'd be open to the idea of a caricature if you can do that within the price.

```html
<!DOCTYPE html>
<html lang="en">
<head>
<meta charset="utf-8">
<title>Unravelling Markets Podcast Cover</title>
<link rel="stylesheet" href="https://fonts.googleapis.com/css2?family=Anton&family=Poppins:wght@500;600&display=swap">
<style>
  :root {
    --yellow-top: #dcae2a;
    --yellow-mid: #ecc832;
    --yellow-bottom: #f8e27a;
    --ink: #0d0c0a;
    --band: #17140f;
    --white: #ffffff;
    --gold: #f5c518;
    --ring: #d8c98a;
    --pig-pink: #e8b39e;
    --pig-shade: #d99480;
  }
  html, body {
    margin: 0;
    padding: 0;
    overflow: hidden;
    background: #f4f4f4;
  }
  .cover {
    position: relative;
    width: 1200px;
    height: 1200px;
    overflow: hidden;
    background: linear-gradient(180deg, var(--yellow-top) 0%, var(--yellow-mid) 45%, var(--yellow-bottom) 100%);
  }
  .cover-art {
    position: absolute;
    inset: 0;
    width: 1200px;
    height: 1200px;
  }
  .title-text {
    font-family: "Anton", "Oswald", sans-serif;
    fill: var(--ink);
  }
  .host-name {
    font-family: "Poppins", sans-serif;
    font-weight: 600;
    font-size: 50px;
    fill: var(--white);
    letter-spacing: -1px;
  }
  .host-role {
    font-family: "Poppins", sans-serif;
    font-weight: 500;
    font-size: 25px;
    fill: var(--gold);
    letter-spacing: 3px;
  }
</style>
</head>
<body>
<main class="cover">
  <svg class="cover-art" viewBox="0 0 1200 1200" xmlns="http://www.w3.org/2000/svg">
    <defs>
      <linearGradient id="pig-tone" x1="0" y1="0" x2="0" y2="1">
        <stop offset="0" stop-color="var(--pig-pink)"/>
        <stop offset="1" stop-color="var(--pig-shade)"/>
      </linearGradient>
      <radialGradient id="host-left-tone" cx="0.5" cy="0.45" r="0.6">
        <stop offset="0" stop-color="#a39a92"/>
        <stop offset="0.6" stop-color="#4a4546"/>
        <stop offset="1" stop-color="#2a2729"/>
      </radialGradient>
      <linearGradient id="host-right-tone" x1="0" y1="0" x2="0" y2="1">
        <stop offset="0" stop-color="#e9ecee"/>
        <stop offset="0.5" stop-color="#d9b4a0"/>
        <stop offset="1" stop-color="#2e8e9e"/>
      </linearGradient>
    </defs>

    <!-- Title block -->
    <g class="title-block">
      <line x1="284" y1="114" x2="535" y2="114" stroke="var(--ink)" stroke-width="3"/>
      <line x1="674" y1="114" x2="925" y2="114" stroke="var(--ink)" stroke-width="3"/>
      <text class="title-text" x="604" y="144" font-size="73" text-anchor="middle" textLength="99" lengthAdjust="spacingAndGlyphs">THE</text>
      <text class="title-text" x="603" y="297" font-size="152" text-anchor="middle" textLength="694" lengthAdjust="spacingAndGlyphs">UNRAVELLING</text>
      <text class="title-text" x="598" y="500" font-size="211" text-anchor="middle" textLength="933" lengthAdjust="spacingAndGlyphs">MARKETS</text>
      <text class="title-text" x="601" y="612" font-size="92" text-anchor="middle" textLength="319" lengthAdjust="spacingAndGlyphs">PODCAST</text>
      <text class="title-text" x="600" y="688" font-size="56" text-anchor="middle" textLength="121" lengthAdjust="spacingAndGlyphs">WITH</text>
    </g>

    <!-- Centre object -->
    <ellipse class="pig-bank" role="img" aria-label="Pink ceramic piggy bank with a bandage on its head" cx="597" cy="878" rx="138" ry="142" fill="url(#pig-tone)"/>

    <!-- Name bands -->
    <polygon class="name-band name-band--left" points="0,975 478,975 385,1161 0,1161" fill="var(--band)"/>
    <polygon class="name-band name-band--right" points="720,975 1200,975 1200,1161 815,1161" fill="var(--band)"/>

    <!-- Host portraits -->
    <g class="host-portrait host-portrait--left">
      <circle cx="248" cy="809" r="188" fill="var(--ring)"/>
      <circle role="img" aria-label="Portrait photo of host Alan Brooke" cx="248" cy="809" r="182" fill="url(#host-left-tone)"/>
    </g>
    <g class="host-portrait host-portrait--right">
      <circle cx="945" cy="809" r="188" fill="var(--ring)"/>
      <circle role="img" aria-label="Portrait photo of host Ray Tolliver" cx="945" cy="809" r="182" fill="url(#host-right-tone)"/>
    </g>

    <!-- Host captions -->
    <text class="host-name" x="79" y="1066">Alan Brooke</text>
    <text class="host-role" x="80" y="1113">PROFESSOR</text>
    <text class="host-name" x="1118" y="1066" text-anchor="end">Ray Tolliver</text>
    <text class="host-role" x="1118" y="1113" text-anchor="end">JOURNALIST</text>
  </svg>
</main>
</body>
</html>
```